Therapeutic Counselling Practice Brochure

I have a new therapeutic counselling practice in Melbourne.

I am making peri natal issues my special interest area.

I need a brochure targeted at new parents or pregnant women and partners, struggling with the concept of parenting, depression, maybe do not even know about it.

The feel should be safe and strong. I love the WREN website ( I do volunteer work with them)

Out of hours appointments and telephone counselling are important making my service very accessible.

Attached is an example for the content of the Brochure

Attached is an example for the content of the Brochure.

Target Market(s)

25 - 45 New Parents , expectant parents,families and friends of people struggling emotionally and mentally with and around being new parents

Requirements
Must have
• Feel of safety, somewhere to go for help, support, a conversation, soft ,strong
Nice to have
• mother and child, maybe parents and child, possibly a graphic, faceless

```html
<!DOCTYPE html>
<html lang="en">
<head>
<meta charset="utf-8">
<title>Depression During and After Pregnancy</title>
<link href="https://fonts.googleapis.com/css2?family=Carlito:ital,wght@0,400;0,700;1,400&display=swap" rel="stylesheet">
<style>
  :root {
    --forest: #3e6a28;
    --lime: #a6cb3c;
    --leaf: #4f7d2c;
    --ink: #2e2e2e;
    --paper: #ffffff;
    --sky: #9fc6e6;
    --mist: #eef2f3;
  }
  * { box-sizing: border-box; margin: 0; padding: 0; }
  html, body { width: 1200px; height: 854px; overflow: hidden; background: var(--paper); }
  body { font-family: "Carlito", "Calibri", sans-serif; color: var(--ink); }
  .brochure { position: relative; width: 1200px; height: 854px; overflow: hidden; background: var(--paper); }
  .band { position: absolute; left: 0; width: 1200px; }
  .band--top { top: 0; height: 130px; }
  .band--bottom { bottom: 0; height: 140px; }
  .panel { position: absolute; }

  .photo { position: absolute; }
  .photo--mother-baby { left: 0; top: 40px; width: 406px; height: 250px;
    background: linear-gradient(100deg, var(--sky) 0%, #d6e6f2 35%, #f3f5f6 60%, #ffffff 100%); }
  .photo--sky { left: 407px; top: 20px; width: 414px; height: 390px;
    background: radial-gradient(ellipse at 70% 55%, #ffffff 0%, #eaf3fa 35%, transparent 70%),
                linear-gradient(180deg, #7fb3e0 0%, #b9d7ef 45%, #ffffff 100%); }
  .photo--consultation { left: 407px; top: 430px; width: 394px; height: 380px;
    background: linear-gradient(90deg, #e9ecee 0%, #f6f7f8 45%, #e8e6e3 70%, #dcdad6 100%); }
  .ornament { position: absolute; left: 930px; top: 120px; width: 250px; height: 640px;
    background: radial-gradient(ellipse at 50% 45%, rgba(150,160,140,0.10) 0%, rgba(150,160,140,0.04) 55%, transparent 75%); }

  .title { position: absolute; left: 44px; top: 118px; font-size: 29px; font-weight: 700;
    line-height: 33px; color: var(--forest); }
  .col-left { left: 40px; top: 266px; width: 330px; font-size: 14.6px; line-height: 19.6px; }
  .col-left p { margin-bottom: 19.6px; }
  .symptoms { list-style: none; }
  .symptoms li { padding-left: 10px; text-indent: -10px; }
  .symptoms li::before { content: "• "; }

  .col-mid { left: 438px; top: 64px; width: 326px; font-size: 14.6px; line-height: 20px; }
  .col-mid p { margin-bottom: 20px; }
  .col-mid p.gap { margin-top: 36px; }
  .quote { font-size: 19px; font-style: italic; line-height: 24px; margin-top: 2px; }
  .quote .speaker { font-size: 15px; font-style: normal; }

  .col-right { left: 830px; top: 60px; width: 336px; font-size: 14.6px; line-height: 19px; }
  .col-right h2 { font-size: 27px; font-weight: 400; color: var(--forest); margin-bottom: 12px; line-height: 30px; }
  .col-right h3 { font-size: 17px; font-weight: 700; color: #333; margin-bottom: 2px; line-height: 22px; }
  .col-right p { margin-bottom: 8px; }
  .col-right .spaced { margin-top: 14px; }
</style>
</head>
<body>
<main class="brochure">
  <svg class="band band--top" viewBox="0 0 1200 130" preserveAspectRatio="none" aria-hidden="true">
    <path d="M0 0 H1200 V20 C900 60 600 30 400 42 C250 50 100 80 0 120 Z" fill="var(--lime)"/>
    <path d="M0 0 H1200 V8 C900 40 600 14 400 28 C250 36 100 60 0 104 Z" fill="var(--forest)"/>
  </svg>

  <div class="photo photo--mother-baby" role="img" aria-label="Soft photograph of a mother holding her newborn baby close"></div>
  <div class="photo photo--sky" role="img" aria-label="Photograph of a blue sky with soft white clouds"></div>
  <div class="photo photo--consultation" role="img" aria-label="Photograph of a doctor listening to a worried young woman"></div>
  <div class="ornament" role="img" aria-label="Faint decorative outline of a mother cradling a child"></div>

  <h1 class="title">DEPRESSION-<br>During and<br>After<br>Pregnancy</h1>

  <section class="panel col-left">
    <p>Depression is more than just the “Baby Blues” (feeling weepy and irritable), or feeling “down in the dumps” for a few days. With depression, sad, anxious or empty feelings don’t go away.</p>
    <p>They interfere with your daily life and routines. The good news is that most people with depression get better with treatment.</p>
    <p style="margin-bottom:19.6px">How do I know if I have depression?<br>If you have any of the following symptoms for more than two weeks:</p>
    <ul class="symptoms">
      <li>Feeling restless or moody</li>
      <li>Feeling sad, hopeless and overwhelmed</li>
      <li>Crying</li>
      <li>Having no energy or motivation</li>
      <li>Eating too much or too little</li>
      <li>Sleeping too much or too little</li>
      <li>Withdrawing from family or friends</li>
      <li>Having memory problems</li>
      <li>Feeling worthless or guilty</li>
      <li>Experiencing headaches, aches and pains</li>
      <li>Having trouble focusing or making decisions</li>
      <li>Losing interest in pleasurable activities you used to enjoy.</li>
    </ul>
  </section>

  <section class="panel col-mid">
    <p>Depression impacts on the whole family, including baby.</p>
    <p>You may feel guilty and a <em>“not good enough mother”</em>, you may lose confidence.</p>
    <p>Depression can be treated with counselling, <em>“talk therapy”</em>. A check up at your doctor is advisable too.</p>
    <p class="gap">Postpartum depression doesn't discriminate.<br>It affects women of all ages, cultural and social standing.</p>
    <p class="quote">“Sometimes”, <span class="speaker">said Bramble</span> “The smallest thing takes up the most room in your heart.”</p>
  </section>

  <section class="panel col-right">
    <h2>Looking after yourself</h2>
    <h3>Rest</h3>
    <p>Sleep if you can, and have a rest if you can't. Nap when your baby is sleeping.</p>
    <h3>Diet</h3>
    <p>Eat a healthy, well-balanced diet . With all the new demands on your body, good nutrition is very important. Try not to skip meals.</p>
    <h3>Exercise</h3>
    <p>Although it may be the last thing you feel like doing; some gentle exercise will help you to feel better both physically and mentally. Just going for a walk with your baby can help.</p>
    <h3 class="spaced">Meditate</h3>
    <p>It may be difficult to quieten your mind; a guided meditation on CD may help.</p>
    <h3>Stay connected</h3>
    <p>Having a baby can make you feel isolated. Meet with other new mothers, join a supportive mothers group.</p>
    <h3>Be kind to yourself</h3>
    <p>You need to take care of yourself to take care of your baby. Don't load yourself up with things that really don't need to be done.<br>Know how little can be enough.</p>
    <h3 class="spaced">Help ..................ask and accept</h3>
    <p>Ask and accept offers of help around the home and with meals.<br>You may not need professional help at the moment, surround yourself with people you can be honest with, share how you are feeling.</p>
  </section>

  <svg class="band band--bottom" viewBox="0 0 1200 140" preserveAspectRatio="none" aria-hidden="true">
    <path d="M0 70 C300 100 700 100 1200 0 V140 H0 Z" fill="var(--lime)"/>
    <path d="M0 96 C350 120 750 110 1200 40 V140 H0 Z" fill="var(--forest)"/>
  </svg>
</main>
</body>
</html>
```